Company director needs a business card design

I am a semi-retired former senior finance executive who sits on a number of public and private company boards and do some consulting work. I work largely with emerging businesses but deal regularly with top end of town lawyers, bankers etc. I need a thoughtful but relatively conservative design which would also resonate with my younger client base. Some colour would be good. Information limited to name, address, office tel, mobile and email.

Finance

```html
<!DOCTYPE html>
<html lang="en">
<head>
<meta charset="utf-8">
<title>Daniel Hart – Business Card</title>
<link rel="stylesheet" href="https://fonts.googleapis.com/css2?family=Noto+Serif:wght@400;700&display=swap">
<style>
  :root {
    --backdrop: #e6e4e0;
    --card-white: #ffffff;
    --card-blue: #8aaefa;
    --ink: #111111;
    --shadow: rgba(0, 0, 0, 0.18);
  }
  * { margin: 0; padding: 0; box-sizing: border-box; }
  html, body {
    width: 1200px;
    height: 800px;
    overflow: hidden;
    background: var(--backdrop);
  }
  .canvas {
    position: relative;
    width: 1200px;
    height: 800px;
    display: flex;
    align-items: center;
    justify-content: center;
  }
  .card {
    position: relative;
    width: 1000px;
    height: 572px;
    background: var(--card-white);
    box-shadow: 0 10px 30px var(--shadow);
    overflow: hidden;
    font-family: "Noto Serif", Georgia, serif;
    color: var(--ink);
  }
  .card__band {
    position: absolute;
    inset: 0;
    width: 100%;
    height: 100%;
  }
  .card__band polygon { fill: var(--card-blue); }
  .identity {
    position: absolute;
    left: 120px;
    top: 92px;
  }
  .identity__name {
    font-size: 50px;
    font-weight: 400;
    letter-spacing: -1px;
    line-height: 1;
  }
  .identity__title {
    font-size: 27px;
    margin-top: 2px;
    margin-left: -8px;
  }
  .contact-row {
    position: absolute;
    display: flex;
    align-items: flex-start;
    font-size: 27px;
    line-height: 1.35;
  }
  .contact-row svg {
    flex: none;
    width: 26px;
    height: 26px;
    fill: var(--ink);
    margin-top: 6px;
  }
  .contact-row--phone { left: 80px; top: 325px; }
  .contact-row--mobile { left: 80px; top: 382px; }
  .contact-row--phone span,
  .contact-row--mobile span { margin-left: 74px; }
  .contact-row--address { left: 580px; top: 330px; }
  .contact-row--address span { margin-left: 48px; }
  .contact-row--email { left: 580px; top: 438px; font-weight: 700; }
  .contact-row--email span { margin-left: 48px; }
</style>
</head>
<body>
<main class="canvas">
  <article class="card">
    <svg class="card__band" viewBox="0 0 1000 572" preserveAspectRatio="none" aria-hidden="true">
      <polygon points="0,205 440,238 446,262 700,300 775,270 1000,300 1000,572 0,572"/>
    </svg>

    <header class="identity">
      <h1 class="identity__name">Daniel Hart</h1>
      <p class="identity__title">Company Director</p>
    </header>

    <div class="contact-row contact-row--phone">
      <svg viewBox="0 0 24 24" aria-label="Office telephone"><path d="M6.6 10.8a15 15 0 0 0 6.6 6.6l2.2-2.2a1 1 0 0 1 1-.25 11.4 11.4 0 0 0 3.6.57 1 1 0 0 1 1 1V20a1 1 0 0 1-1 1A17 17 0 0 1 3 4a1 1 0 0 1 1-1h3.5a1 1 0 0 1 1 1c0 1.25.2 2.45.57 3.57a1 1 0 0 1-.25 1z"/></svg>
      <span>+1 (555) 0142 730</span>
    </div>

    <div class="contact-row contact-row--mobile">
      <svg viewBox="0 0 24 24" aria-label="Mobile"><path d="M7 2h10a2 2 0 0 1 2 2v16a2 2 0 0 1-2 2H7a2 2 0 0 1-2-2V4a2 2 0 0 1 2-2zm0 3v13h10V5zm5 14.2a.9.9 0 1 0 0 1.8.9.9 0 0 0 0-1.8z"/></svg>
      <span>+1 (555) 0142 731</span>
    </div>

    <div class="contact-row contact-row--address">
      <svg viewBox="0 0 24 24" aria-label="Address"><path d="M12 2a7 7 0 0 0-7 7c0 5.2 7 13 7 13s7-7.8 7-13a7 7 0 0 0-7-7zm0 9.5A2.5 2.5 0 1 1 12 6.5a2.5 2.5 0 0 1 0 5z"/></svg>
      <span>48 Harbor Rd., Millbrook,<br>NY 10032<br>P.O. Box: 204816</span>
    </div>

    <div class="contact-row contact-row--email">
      <svg viewBox="0 0 24 24" aria-label="Email"><path d="M3 5h18a1 1 0 0 1 1 1v.4l-10 6.3L2 6.4V6a1 1 0 0 1 1-1zm-1 3.7 10 6.3 10-6.3V18a1 1 0 0 1-1 1H3a1 1 0 0 1-1-1z"/></svg>
      <span>mail@example.com</span>
    </div>
  </article>
</main>
</body>
</html>
```